Create a business promotion flyer to leave in customer mailboxes. We are a bulk petroleum supplier, servicing any industry that requires diesel. Base in griffith NSW, servicing griffith area and surrounds.

Business Name - Terra Diesel
Fuel@terradiesel-example.com.au
Owen - 0491 570 362 ohartley@terradiesel-example.com.au
Liam - 0491 570 718 lprosser@terradiesel-example.com.au
Simon - 0491 570 905 skenway@terradiesel-example.com.au
Office 02 5550 1734

Bulk Fuel deliveries.
Oils & lubricants
Local Family owned business

```html
<!DOCTYPE html>
<html lang="en">
<head>
<meta charset="utf-8">
<title>Terra Diesel – Bulk Petroleum Supplier Flyer</title>
<link rel="stylesheet" href="https://fonts.googleapis.com/css2?family=Montserrat:wght@800&family=Josefin+Sans:ital,wght@0,600;1,400&family=Oswald:wght@300;400;500;600&family=Poppins:wght@600&display=swap">
<style>
  :root {
    --mat: #a7a8aa;
    --red: #e0261f;
    --red-light: #ee5a48;
    --grey: #666667;
    --grey-dark: #58595b;
    --grey-text: #5a5b5d;
    --white: #ffffff;
    --paper: #f4f4f4;
  }
  * { margin: 0; padding: 0; box-sizing: border-box; }
  html, body { width: 980px; height: 1200px; overflow: hidden; }
  body { background: var(--mat); position: relative; font-family: "Oswald", sans-serif; }

  .flyer {
    position: absolute; left: 90px; top: 86px; width: 804px; height: 1042px;
    background: var(--paper); overflow: hidden;
  }
  .backdrop-photo {
    position: absolute; inset: 0 0 300px 0;
    background: linear-gradient(180deg, #f1f1f1 0%, #d9d9d9 45%, #c9c9c9 70%, #f2f2f2 100%);
  }
  .hero-shape { position: absolute; left: 0; top: 0; }

  .logo-tab {
    position: absolute; left: 302px; top: -2px; width: 204px; height: 197px;
    background: linear-gradient(180deg, #ffffff 60%, #ececec 100%);
    border: 1.5px solid #5e5e5e; border-top: none;
    border-radius: 0 0 102px 102px;
    display: flex; align-items: center; justify-content: center; gap: 6px;
  }
  .logo-tab .brand-dot { width: 12px; height: 12px; border-radius: 50%; background: var(--red); }
  .logo-tab .brand-name { font-family: "Josefin Sans", sans-serif; font-weight: 600; font-size: 25px; color: var(--red); margin-top: 4px; }

  .headline {
    position: absolute; left: 0; width: 804px; top: 213px; text-align: center;
    font-family: "Montserrat", sans-serif; font-weight: 800; font-size: 66px;
    letter-spacing: -1px; color: var(--white); line-height: 1;
    text-shadow: 0 2px 3px rgba(0,0,0,0.18);
  }
  .tagline {
    position: absolute; left: 0; width: 804px; top: 290px; text-align: center;
    font-family: "Josefin Sans", sans-serif; font-style: italic; font-size: 35px; color: var(--white); letter-spacing: 1px;
  }
  .subtagline {
    position: absolute; left: 0; width: 800px; top: 333px; text-align: center;
    font-family: "Josefin Sans", sans-serif; font-style: italic; font-size: 21px; color: var(--white);
  }
  .values {
    position: absolute; left: 160px; top: 377px; display: flex; gap: 22px;
    font-family: "Josefin Sans", sans-serif; font-size: 22px; color: var(--white); list-style: none;
  }
  .values li { display: flex; align-items: center; gap: 5px; }
  .values svg { width: 20px; height: 20px; margin-top: -4px; }

  .truck-photo {
    position: absolute; left: 0; top: 430px; width: 804px; height: 266px;
    background: linear-gradient(180deg, #9ea4ab 0%, #c7ccd1 30%, #eef0f1 55%, #d8dadc 78%, #eeeeee 100%);
  }

  .lower-shapes { position: absolute; left: 0; top: 0; }

  .base-badge {
    position: absolute; left: 69px; top: 677px; width: 186px; height: 186px;
    border-radius: 50%; border: 3px solid var(--red); background: var(--grey);
    padding: 5px;
  }
  .base-badge .map {
    width: 100%; height: 100%; border-radius: 50%;
    background: radial-gradient(circle at 45% 40%, #f3f3f3 0%, #e1e1e1 100%);
    display: flex; flex-direction: column; align-items: center; padding-top: 38px;
  }
  .base-badge .lead { font-weight: 500; font-size: 21px; color: var(--red); line-height: 1; }
  .base-badge .town { font-weight: 600; font-size: 34px; color: var(--red); line-height: 1.05; }
  .base-badge .state { font-weight: 500; font-size: 27px; color: var(--grey-text); line-height: 1; }
  .base-badge svg { margin-top: 8px; width: 24px; height: 32px; }

  .service-icon { position: absolute; left: 270px; top: 688px; width: 92px; height: 78px; }
  .service-area {
    position: absolute; left: 271px; top: 768px; font-weight: 500; font-size: 22px;
    line-height: 27px; color: var(--grey-text); letter-spacing: 0.5px;
  }

  .offer-card {
    position: absolute; left: 461px; top: 699px; width: 317px; height: 248px;
    border-radius: 48px 48px 0 0;
    background: linear-gradient(150deg, var(--red-light) 0%, var(--red) 30%, var(--red) 100%);
    border: 4px solid var(--red); border-bottom: none;
    box-shadow: 0 2px 6px rgba(0,0,0,0.15);
  }
  .offer-card ul { list-style: none; position: absolute; left: 26px; top: 52px; }
  .offer-card li {
    display: flex; align-items: flex-start; gap: 8px;
    font-weight: 500; font-style: italic; font-size: 30px; line-height: 39px; color: var(--white);
  }
  .offer-card li svg { width: 26px; height: 26px; flex: none; margin-top: 7px; }

  .email-bar {
    position: absolute; left: 0; top: 884px; width: 366px; height: 41px;
    background: var(--red); border-radius: 0 22px 22px 0;
    display: flex; align-items: center; padding-left: 44px; gap: 7px;
    font-family: "Poppins", sans-serif; font-weight: 600; font-size: 16px; color: var(--white);
  }
  .email-bar svg { width: 24px; height: 17px; flex: none; }

  .contacts {
    position: absolute; left: 0; top: 962px; width: 804px; height: 58px;
    display: flex; color: var(--white);
  }
  .contact { padding-left: 45px; width: 240px; font-weight: 300; font-size: 11.5px; line-height: 19px; white-space: nowrap; }
  .contact + .contact { border-left: 1px solid #9d9d9e; padding-left: 29px; }
  .contact:nth-child(2) { width: 206px; }
  .contact:nth-child(3) { width: 196px; padding-left: 20px; }
  .contact:nth-child(4) { width: 162px; padding-left: 21px; padding-top: 10px; }
  .contact .who { font-weight: 500; font-size: 16px; line-height: 20px; }
  .contact .phone { font-size: 16px; }
</style>
</head>
<body>
<main class="flyer">
  <div class="backdrop-photo" role="img" aria-label="Faded grey aerial photo of a fuel refinery with storage tanks"></div>

  <svg class="hero-shape" width="804" height="700" viewBox="0 0 804 700" aria-hidden="true">
    <circle cx="402" cy="356" r="322" fill="var(--grey)"/>
    <circle cx="402" cy="356" r="306" fill="var(--white)"/>
    <circle cx="402" cy="356" r="297" fill="var(--red)"/>
  </svg>

  <div class="logo-tab">
    <span class="brand-dot"></span><span class="brand-name">Terra Diesel</span>
  </div>

  <h1 class="headline">TERRA DIESEL</h1>
  <p class="tagline">Bulk petroleum supplier</p>
  <p class="subtagline">Your Diesel Supply Partner</p>
  <ul class="values">
    <li><svg viewBox="0 0 20 20"><circle cx="10" cy="10" r="10" fill="#fff"/><path d="M5.5 10.3l3 3 6-6.2" stroke="var(--red)" stroke-width="2.4" fill="none" stroke-linecap="round" stroke-linejoin="round"/></svg>RELIABLE</li>
    <li><svg viewBox="0 0 20 20"><circle cx="10" cy="10" r="10" fill="#fff"/><path d="M5.5 10.3l3 3 6-6.2" stroke="var(--red)" stroke-width="2.4" fill="none" stroke-linecap="round" stroke-linejoin="round"/></svg>LOCAL</li>
    <li><svg viewBox="0 0 20 20"><circle cx="10" cy="10" r="10" fill="#fff"/><path d="M5.5 10.3l3 3 6-6.2" stroke="var(--red)" stroke-width="2.4" fill="none" stroke-linecap="round" stroke-linejoin="round"/></svg>READY TO DELIVER</li>
  </ul>

  <div class="truck-photo" role="img" aria-label="Photo of a white road-train fuel tanker truck with two tanker trailers parked in front of a steel depot shed"></div>

  <svg class="lower-shapes" width="804" height="1042" viewBox="0 0 804 1042" aria-hidden="true">
    <path d="M0 800 Q60 880 190 884 L0 884 Z" fill="var(--grey)"/>
    <path d="M0 918 L0 1042 L804 1042 L804 950 Q560 955 440 930 Q380 918 330 918 Z" fill="var(--grey)"/>
  </svg>

  <div class="base-badge">
    <div class="map" role="img" aria-label="Light grey map of New South Wales">
      <span class="lead">BASED IN</span>
      <span class="town">GRIFFITH</span>
      <span class="state">NSW</span>
      <svg viewBox="0 0 24 32"><path d="M12 1C6 1 1.5 5.5 1.5 11.3 1.5 19 12 31 12 31s10.5-12 10.5-19.7C22.5 5.5 18 1 12 1z" fill="var(--red)"/><circle cx="12" cy="11" r="4.3" fill="#e6e6e6"/></svg>
    </div>
  </div>

  <svg class="service-icon" viewBox="0 0 92 78" aria-hidden="true">
    <path d="M40 4 A40 40 0 0 1 70 70" stroke="var(--grey-dark)" stroke-width="2.5" fill="none"/>
    <path d="M46 9 A34 34 0 0 1 72 58" stroke="var(--red)" stroke-width="2.5" fill="none"/>
    <rect x="24" y="24" width="50" height="32" fill="#fff" stroke="#222" stroke-width="2.4"/>
    <path d="M24 34 H11 L4 45 V60 H24 Z" fill="#fff" stroke="#222" stroke-width="2.4" stroke-linejoin="round"/>
    <path d="M9 37 H20 V45 H5" fill="none" stroke="#222" stroke-width="2"/>
    <path d="M24 60 H76" stroke="#222" stroke-width="2.4"/>
    <circle cx="14" cy="62" r="4.5" fill="#fff" stroke="#222" stroke-width="2.4"/>
    <circle cx="52" cy="62" r="4.5" fill="#fff" stroke="#222" stroke-width="2.4"/>
    <circle cx="64" cy="62" r="4.5" fill="#fff" stroke="#222" stroke-width="2.4"/>
  </svg>
  <p class="service-area">SERVICING<br>GRIFFITH AREA<br>&amp; SURROUNDS</p>

  <section class="offer-card">
    <ul>
      <li><svg viewBox="0 0 20 20"><circle cx="10" cy="10" r="10" fill="#fff"/><path d="M5.5 10.3l3 3 6-6.2" stroke="var(--red)" stroke-width="2.4" fill="none" stroke-linecap="round" stroke-linejoin="round"/></svg>Bulk Fuel deliveries</li>
      <li><svg viewBox="0 0 20 20"><circle cx="10" cy="10" r="10" fill="#fff"/><path d="M5.5 10.3l3 3 6-6.2" stroke="var(--red)" stroke-width="2.4" fill="none" stroke-linecap="round" stroke-linejoin="round"/></svg>Oils &amp; lubricants</li>
      <li><svg viewBox="0 0 20 20"><circle cx="10" cy="10" r="10" fill="#fff"/><path d="M5.5 10.3l3 3 6-6.2" stroke="var(--red)" stroke-width="2.4" fill="none" stroke-linecap="round" stroke-linejoin="round"/></svg>Local Family owned<br>business</li>
    </ul>
  </section>

  <div class="email-bar">
    <svg viewBox="0 0 24 17"><rect x="1" y="1" width="22" height="15" fill="none" stroke="#fff" stroke-width="1.6"/><path d="M1 1 L12 10 L23 1 M1 16 L9 8 M23 16 L15 8" fill="none" stroke="#fff" stroke-width="1.4"/></svg>
    Fuel@terradiesel-example.com.au
  </div>

  <footer class="contacts">
    <div class="contact"><div class="who">Owen</div><div class="phone">0491 570 362</div><div>ohartley@terradiesel-example.com.au</div></div>
    <div class="contact"><div class="who">Liam</div><div class="phone">0491 570 718</div><div>lprosser@terradiesel-example.com.au</div></div>
    <div class="contact"><div class="who">Simon</div><div class="phone">0491 570 905</div><div>skenway@terradiesel-example.com.au</div></div>
    <div class="contact"><div class="who">Office</div><div class="phone">02 5550 1734</div></div>
  </footer>
</main>
</body>
</html>
```